Design a Poster to Advertise Pip'n'Crumbo at the Netball Stadium

Objective:
Create an eye-catching and enticing poster to promote Pip'n'Crumbo, a ready-to-eat snack, at a netball stadium where large numbers of players, families, and friends gather weekly. The goal is to attract attention, stimulate appetite, and encourage purchases from both kids and adults.
Key Elements to Include:
Company Logo:
Incorporate our logo prominently to ensure brand recognition.
Product Description:
Feature a mouth-watering description: "Deliciously cheesy, oozy mac'n'cheese hand-rolled into bite-sized balls and coated in a crispy, crunchy panko crumb." This should be paired with an enticing image of the product.
Serving Suggestion:
Include a high-quality image showing Pip'n'Crumbo balls served in an appealing way. The visual should highlight the crispy exterior and gooey interior to emphasize the product's deliciousness.
Catchy Tagline or Slogan:
Develop a fun and engaging tagline that appeals to kids and encourages them to persuade their parents to buy the product. For example, “Grab a Cheesy Treat Today!” or “The Snack Everyone's Cheering For!”
Visual Appeal:
Use vibrant colors and dynamic design elements to draw attention. The poster should create a visual feast that makes Pip'n'Crumbo irresistible.
Include essential details such as:
The location where Pip'n'Crumbo will be available at the stadium.
Pricing information if relevant.
Promote that is locally South Australian made with all natural ingredients
Call to Action:
Add a compelling call to action that encourages immediate purchase, such as “Get Yours Now!” or “Don’t Miss Out!”
Layout:
Ensure the design is clean and organized, with a clear hierarchy of information. The poster should be easy to read from a distance.
Design Specifications:
Size: A3 or larger
Notes:
The poster should appeal to both children and adults, emphasizing the irresistible taste and texture of Pip'n'Crumbo. The design should make the product a must-have snack at the netball stadium.
Target Market(s)
10 year olds to 18 year olds
Industry/Entity Type
food
Look and feel
Each slider illustrates characteristics of the customer's brand and the style your logo design should communicate.

```html
<!DOCTYPE html>
<html lang="en">
<head>
<meta charset="UTF-8">
<title>Pip'n'Crumbo – Grab a Cheesy Treat Today</title>
<link href="https://fonts.googleapis.com/css2?family=Bowlby+One&family=Montserrat:wght@600;700&display=swap" rel="stylesheet">
<style>
  :root {
    --sun-yellow: #FFDF00;
    --soft-yellow: #F7E24A;
    --tomato: #EF4A2E;
    --headline-red: #E8452C;
    --pitch-green: #17735E;
    --crumb-gold: #D9A040;
    --board-brown: #8A5A3A;
    --ink: #1A1A1A;
  }
  * { margin: 0; padding: 0; box-sizing: border-box; }
  html, body { width: 900px; height: 1200px; overflow: hidden; background: var(--sun-yellow); }
  .poster {
    position: relative;
    width: 900px;
    height: 1200px;
    background: var(--sun-yellow);
    overflow: hidden;
    font-family: "Montserrat", Arial, sans-serif;
  }
  .brand {
    position: absolute;
    top: 84px;
    left: 0;
    width: 100%;
    display: flex;
    justify-content: center;
    align-items: center;
    gap: 12px;
  }
  .brand-mark {
    width: 18px;
    height: 18px;
    border-radius: 50%;
    background: var(--ink);
  }
  .brand-name {
    font-family: "Montserrat", Arial, sans-serif;
    font-weight: 700;
    font-size: 34px;
    color: var(--ink);
    letter-spacing: 1px;
  }
  .headline {
    position: absolute;
    top: 222px;
    left: 0;
    width: 100%;
    text-align: center;
    font-family: "Bowlby One", "Arial Black", sans-serif;
    font-weight: 400;
    line-height: 1;
    letter-spacing: 3px;
  }
  .headline-top { display: block; font-size: 60px; color: var(--headline-red); }
  .headline-bottom { display: block; font-size: 60px; color: var(--pitch-green); margin-top: -4px; }
  .description {
    position: absolute;
    top: 350px;
    left: 0;
    width: 100%;
    text-align: center;
    font-weight: 600;
    font-size: 20px;
    line-height: 1.2;
    color: var(--headline-red);
  }
  .description strong { font-weight: 700; }
  .court-scene {
    position: absolute;
    left: 440px;
    top: 400px;
    width: 460px;
    height: 500px;
    background: linear-gradient(180deg, var(--sun-yellow) 0%, var(--soft-yellow) 60%, #E2C634 100%);
    opacity: 0.9;
  }
  .red-wave {
    position: absolute;
    left: 0;
    top: 840px;
    width: 900px;
    height: 360px;
  }
  .snack-photo {
    position: absolute;
    left: 0;
    top: 440px;
    width: 760px;
    height: 570px;
    border-radius: 0 60px 140px 0;
    background: radial-gradient(ellipse at 45% 40%, var(--crumb-gold) 0%, #C8863A 45%, var(--board-brown) 100%);
  }
  .burst { position: absolute; left: 730px; top: 990px; width: 80px; height: 70px; }
  .cta {
    position: absolute;
    left: 228px;
    top: 1044px;
    width: 460px;
    height: 74px;
    border-radius: 14px;
    background: var(--sun-yellow);
    display: flex;
    align-items: center;
    justify-content: center;
    font-family: "Bowlby One", "Arial Black", sans-serif;
    font-size: 34px;
    color: var(--tomato);
    letter-spacing: 1px;
  }
</style>
</head>
<body>
<main class="poster">
  <header class="brand">
    <span class="brand-mark"></span>
    <span class="brand-name">Dorato Bocconi</span>
  </header>

  <div class="court-scene" role="img" aria-label="Sketched netball court with a net, post, ball and clouds in yellow tones"></div>

  <h1 class="headline">
    <span class="headline-top">GRAB A CHEESY</span>
    <span class="headline-bottom">TREAT TODAY!</span>
  </h1>

  <p class="description">
    Deliciously cheesy, oozy <strong>mac'n'cheese</strong><br>
    hand-rolled into bite-sized balls and coated<br>
    in a crispy, crunchy panko crumb.
  </p>

  <svg class="red-wave" viewBox="0 0 900 360" preserveAspectRatio="none" aria-hidden="true">
    <path d="M0 120 C 40 110, 70 160, 80 230 C 90 300, 60 330, 0 345 L0 360 L900 360 L900 0 C 820 10, 760 0, 700 30 C 620 70, 520 40, 420 80 C 300 120, 200 100, 120 110 C 80 115, 40 100, 0 120 Z" fill="var(--tomato)"/>
  </svg>

  <div class="snack-photo" role="img" aria-label="Photo of golden panko-crumbed Pip'n'Crumbo balls piled on a wooden board with scattered crumbs"></div>

  <svg class="burst" viewBox="0 0 80 70" aria-hidden="true">
    <g stroke="var(--sun-yellow)" stroke-width="6" stroke-linecap="round">
      <line x1="8" y1="38" x2="20" y2="62"/>
      <line x1="36" y1="4" x2="44" y2="34"/>
      <line x1="58" y1="30" x2="74" y2="20"/>
    </g>
  </svg>

  <div class="cta">DON’T MISS OUT!</div>
</main>
</body>
</html>
```